Civora88 - a Political Plebescite app.

There is a current app in the App Store (worldwide) and Play Store (worldwide) called yourStance (with an owl logo). The UX needs to be redesigned to make it more visually pleasing.

The requirement is to build a UX that is suitable for both iOS and Android - i.e. consistent look for both platforms. The design is to span the variety of sizes available from smart devices - phones and tablets. The layout as it stands is portrait only, and a secondary design to encompass landscape is wanted.

You would need to download the app to get a feel for all the functionality - there are 3 visible forms (currently) and a hidden form, that will be used in the near future - this hidden form will look similar to the main (first) form.

To get full functionality you need to do the following:
Go to the Options page
Toggle the top slide
Click on UNREGISTERED
Select a state/territory

I know this is a bit non-intuitive - in the "real" product these steps are automated - but for this release the user gets to choose.

Once this is done - the other button(s) appear in the top left of the screen - and data is available to be displayed.

The current forms are included in this brief. The Options screen will ultimately not be showing all the current data, only the lower slider (or other indicator) and the associated version and copyright notices. The hidden screen is much like the main screen - showing the name of the bill and information pertaining to that bill - there needs to be a button (or action site) to toggle between the main and this hidden screen.

Target Market(s)

All eligable voters (currently in Australia)

Industry/Entity Type

Political

Requirements
Should not have
• Do not present to me my own/existing design with the only change being colours and label layout.

```html
<!DOCTYPE html>
<html lang="en">
<head>
<meta charset="utf-8">
<title>Civora88 – Bill Screens</title>
<link href="https://fonts.googleapis.com/css2?family=Roboto:wght@300;400;500;700&display=swap" rel="stylesheet">
<style>
  :root {
    --page-bg: #ffffff;
    --screen-bg: #f7f7f8;
    --card-bg: #ffffff;
    --blue: #0a7bff;
    --ink: #1d1d1f;
    --ink-soft: #3a3a3c;
    --rule: #d2d2d6;
    --bar-grey: #efefef;
    --online: #2ecc71;
    --vote-yes: #2ecc71;
    --vote-abstain: #f5d66d;
    --vote-no: #ec6549;
    --icon-dark: #1e1e1e;
  }
  * { box-sizing: border-box; margin: 0; padding: 0; }
  html, body { width: 1200px; height: 1200px; overflow: hidden; }
  body {
    background: var(--page-bg);
    font-family: "Roboto", Arial, sans-serif;
    color: var(--ink);
    display: flex;
    justify-content: center;
    align-items: center;
    gap: 44px;
  }
  .screen {
    width: 540px;
    height: 940px;
    background: var(--screen-bg);
    border: 1px solid var(--rule);
    display: flex;
    flex-direction: column;
  }
  .status-bar {
    height: 34px;
    display: flex;
    align-items: center;
    justify-content: space-between;
    padding: 0 10px;
    font-size: 16px;
  }
  .status-bar .time { font-weight: 700; }
  .signal { display: flex; align-items: center; gap: 3px; }
  .signal i { width: 8px; height: 8px; border-radius: 50%; background: var(--ink); display: block; }
  .battery { display: flex; align-items: center; gap: 4px; font-weight: 300; }
  .battery-cell { width: 36px; height: 15px; border-radius: 3px; background: var(--ink); position: relative; }
  .battery-cell::after { content: ""; position: absolute; right: -4px; top: 5px; width: 3px; height: 5px; background: var(--ink); border-radius: 0 1px 1px 0; }

  .app-header {
    height: 82px;
    border-bottom: 1px solid var(--rule);
    display: grid;
    grid-template-columns: 1fr auto 1fr;
    align-items: end;
    padding: 0 18px 12px;
  }
  .online { display: flex; align-items: center; gap: 9px; font-size: 16px; padding-bottom: 4px; }
  .online::before { content: ""; width: 12px; height: 12px; border-radius: 50%; background: var(--online); }
  .gov-select { text-align: center; }
  .gov-select .label { font-size: 11px; font-weight: 700; letter-spacing: .2px; margin-bottom: 6px; }
  .gov-select .value { font-size: 23px; font-weight: 300; display: flex; align-items: center; gap: 12px; }
  .gov-select .value::before { content: ""; border: 6px solid transparent; border-top: 6px solid var(--ink); border-bottom: 0; }
  .settings { justify-self: end; color: var(--blue); font-size: 20px; font-weight: 300; padding-bottom: 2px; }

  .content { padding: 36px 32px 0; display: flex; flex-direction: column; align-items: stretch; }
  .chamber-toggle {
    display: flex;
    height: 46px;
    border: 2px solid var(--blue);
    border-radius: 5px;
    overflow: hidden;
    font-size: 18px;
    font-weight: 300;
  }
  .chamber-toggle span { flex: 1; display: flex; align-items: center; justify-content: center; color: var(--blue); background: #fff; }
  .chamber-toggle .active { background: var(--blue); color: #fff; }

  .counter { text-align: center; font-weight: 700; font-size: 21px; margin: 30px 0 30px; }

  .bill-stack { position: relative; }
  .bill-card {
    position: relative;
    z-index: 3;
    background: var(--card-bg);
    border-radius: 8px;
    overflow: hidden;
    box-shadow: 0 1px 3px rgba(0,0,0,.2);
  }
  .bill-title {
    background: var(--blue);
    color: #fff;
    font-weight: 700;
    font-size: 20px;
    line-height: 1.25;
    padding: 20px 24px 16px;
  }
  .bill-title .year { display: block; margin-top: 16px; }
  .bill-summary {
    height: 244px;
    padding: 26px 28px;
    font-size: 22px;
    font-weight: 300;
    line-height: 1.3;
    color: var(--ink-soft);
  }
  .view-bill {
    height: 66px;
    background: var(--bar-grey);
    border-top: 1px solid #dcdcdc;
    display: flex;
    align-items: center;
    justify-content: center;
    font-weight: 700;
    font-size: 22px;
    color: var(--ink-soft);
  }
  .stack-layer {
    position: absolute;
    left: 8px; right: 8px;
    height: 40px;
    bottom: -10px;
    background: var(--bar-grey);
    border-radius: 8px;
    box-shadow: 0 1px 2px rgba(0,0,0,.2);
    z-index: 2;
  }
  .stack-layer.back { left: 16px; right: 16px; bottom: -20px; z-index: 1; }

  .vote-bar { display: flex; justify-content: center; gap: 36px; margin-top: 66px; }
  .vote {
    width: 112px; height: 112px;
    border-radius: 50%;
    background: #fff;
    border: 1px solid #dcdcdc;
    box-shadow: 0 1px 3px rgba(0,0,0,.12);
    display: flex; align-items: center; justify-content: center;
  }
  .vote span { width: 100px; height: 100px; border-radius: 50%; display: flex; align-items: center; justify-content: center; }
  .vote-yes span { background: var(--vote-yes); }
  .vote-abstain span { background: var(--vote-abstain); }
  .vote-no span { background: var(--vote-no); }
  .vote svg { width: 44px; height: 44px; fill: var(--icon-dark); }
</style>
</head>
<body>

<section class="screen">
  <div class="status-bar">
    <div class="signal"><i></i><i></i><i></i><i></i><i></i></div>
    <div class="time">9:41 AM</div>
    <div class="battery">100%<span class="battery-cell"></span></div>
  </div>
  <header class="app-header">
    <div class="online">ONLINE</div>
    <div class="gov-select"><div class="label">SELECT GOVERNMENT</div><div class="value">New South Wales</div></div>
    <div class="settings">Settings</div>
  </header>
  <main class="content">
    <div class="chamber-toggle"><span class="active">LEGISLATIVE ASSEMBLY</span><span>LEGISLATIVE COUNCIL</span></div>
    <div class="counter">4/10</div>
    <div class="bill-stack">
      <article class="bill-card">
        <h2 class="bill-title">Monitoring of Places of Detention (Optional Protocol to the Convention Against Torture) - National Uniform Legislation <span class="year">Bill 2013</span></h2>
        <p class="bill-summary">An act to enable the Optional Protocol to the Convention against Torture and other Cruel, Inhuman or Degrading Treatment or Punishment to be given effect within the Territory.</p>
        <div class="view-bill">VIEW BILL</div>
      </article>
      <div class="stack-layer"></div><div class="stack-layer back"></div>
    </div>
    <div class="vote-bar">
      <div class="vote vote-yes"><span><svg viewBox="0 0 24 24" aria-label="Support"><path d="M2 10h4v11H2zM8 21V10l5-7c1.2 0 2 .9 2 2l-1 5h6c1.1 0 2 .9 2 2l-2 7c-.3 1.2-1.2 2-2.4 2z"/></svg></span></div>
      <div class="vote vote-abstain"><span><svg viewBox="0 0 24 24" aria-label="Abstain"><path d="M12 2 2 7v2h20V7zM4 11h2v7H4zm4 0h2v7H8zm4 0h2v7h-2zm4 0h2v7h-2zM2 19h20v3H2z"/></svg></span></div>
      <div class="vote vote-no"><span><svg viewBox="0 0 24 24" aria-label="Oppose"><path d="M2 3h4v11H2zM8 3v11l5 7c1.2 0 2-.9 2-2l-1-5h6c1.1 0 2-.9 2-2l-2-7c-.3-1.2-1.2-2-2.4-2z"/></svg></span></div>
    </div>
  </main>
</section>

<section class="screen">
  <div class="status-bar">
    <div class="signal"><i></i><i></i><i></i><i></i><i></i></div>
    <div class="time">9:41 AM</div>
    <div class="battery">100%<span class="battery-cell"></span></div>
  </div>
  <header class="app-header">
    <div class="online">ONLINE</div>
    <div class="gov-select"><div class="label">SELECT GOVERNMENT</div><div class="value">Central</div></div>
    <div class="settings">Settings</div>
  </header>
  <main class="content">
    <div class="chamber-toggle"><span class="active">THE HOUSE</span><span>THE SENATE</span></div>
    <div class="counter">4/10</div>
    <div class="bill-stack">
      <article class="bill-card">
        <h2 class="bill-title">Monitoring of Places of Detention (Optional Protocol to the Convention Against Torture) - National Uniform Legislation <span class="year">Bill 2013</span></h2>
        <p class="bill-summary">An act to enable the Optional Protocol to the Convention against Torture and other Cruel, Inhuman or Degrading Treatment or Punishment to be given effect within the Territory.</p>
        <div class="view-bill">VIEW BILL</div>
      </article>
      <div class="stack-layer"></div><div class="stack-layer back"></div>
    </div>
    <div class="vote-bar">
      <div class="vote vote-yes"><span><svg viewBox="0 0 24 24" aria-label="Support"><path d="M2 10h4v11H2zM8 21V10l5-7c1.2 0 2 .9 2 2l-1 5h6c1.1 0 2 .9 2 2l-2 7c-.3 1.2-1.2 2-2.4 2z"/></svg></span></div>
      <div class="vote vote-abstain"><span><svg viewBox="0 0 24 24" aria-label="Abstain"><path d="M12 2 2 7v2h20V7zM4 11h2v7H4zm4 0h2v7H8zm4 0h2v7h-2zm4 0h2v7h-2zM2 19h20v3H2z"/></svg></span></div>
      <div class="vote vote-no"><span><svg viewBox="0 0 24 24" aria-label="Oppose"><path d="M2 3h4v11H2zM8 3v11l5 7c1.2 0 2-.9 2-2l-1-5h6c1.1 0 2-.9 2-2l-2-7c-.3-1.2-1.2-2-2.4-2z"/></svg></span></div>
    </div>
  </main>
</section>

</body>
</html>
```